Business Cards for new orthopaedic surgery practice

My husband and I are starting our own orthopaedic surgery practice. We are looking for a business card that is uniform, but one will have my name/title and the other will have his. You can just create one design with my name on it for now. But when I choose your design as the winning design I will ask that you add another copy with his name/title.

We are looking for classy, simple, elite all in one. We like dark blues/a little gold/yellow. Something that goes with our logo. We want our logo incorporated. Here is all the info you need:
Business name: RV Bone & Vitality Center
Location: 38517 North Willowmere Ave
Maple Hollow, FL 33990
Phone: 954-218-4063
Fax: 954-582-7341
Email: info@myrvbonecare.example

Names: Lydia Vance, M.D.
Board Certified Hand and Upper Extremity Surgeon

Ebo Dansu, M.D.
Board Certified Hip & Knee Replacement/General Orthopaedic Surgeon

Can decide what you want to put on the back. Maybe a slogan:
Grounded in Care. Centered on You

I am just going to upload our logo. The only thing is if we select you as the winning design, the location, and phone numbers may change. We will need your help to update that once fully solidified.

Industry/Entity Type

Medical

Contact Information for Business Card

Colors
0054AA
0677BA
7BADD7
CADEEF
E8F1F8
0094D4
00A9DD
6FCCEA
C7EBF8
E9F6FB

Requirements
Must have
• class, appeal,
Should not have
• We want to air on the side of masculine if we are looking at masculine vs. feminine feel. But we still want it classy, sophisticated, and something we will love

```html
<!DOCTYPE html>
<html lang="en">
<head>
<meta charset="utf-8">
<title>RV Bone &amp; Vitality Center – Business Card</title>
<link rel="stylesheet" href="https://fonts.googleapis.com/css2?family=Libre+Caslon+Text:wght@700&family=Arimo:wght@400&display=swap">
<style>
  :root {
    --page: #e4e4e4;
    --navy: #1c2a55;
    --navy-light: #263763;
    --navy-deep: #1a2750;
    --gold: #c9a46a;
    --white: #ffffff;
    --emboss: #3a55a0;
  }
  * { margin: 0; padding: 0; box-sizing: border-box; }
  html, body { width: 1200px; height: 1200px; overflow: hidden; background: var(--page); }
  body { position: relative; font-family: "Arimo", Arial, sans-serif; }

  .card { position: absolute; width: 688px; height: 392px; overflow: hidden; }

  .card-front { left: 267px; top: 159px; background: var(--white); }
  .front-band { position: absolute; left: 0; top: 181px; width: 100%; height: 188px; background: var(--navy); }

  .doctor-name {
    position: absolute; left: 45px; top: 58px;
    font-family: "Libre Caslon Text", Georgia, serif; font-weight: 700;
    font-size: 23px; letter-spacing: 0.5px; color: var(--navy);
  }
  .doctor-title {
    position: absolute; left: 45px; top: 92px;
    font-size: 15px; line-height: 19px; color: var(--gold);
  }

  .contact { position: absolute; left: 45px; top: 212px; color: var(--white); font-size: 16px; }
  .address { line-height: 21px; margin-bottom: 14px; }
  .contact-list { list-style: none; }
  .contact-list li { display: flex; align-items: center; height: 20.5px; }
  .contact-list svg { width: 14px; height: 14px; margin-right: 12px; fill: var(--gold); flex: none; }

  .practice-mark {
    position: absolute; right: 30px; top: 210px; width: 240px; height: 140px;
    display: flex; flex-direction: column; align-items: center; justify-content: center; gap: 14px;
  }
  .practice-dot { width: 22px; height: 22px; border-radius: 50%; background: var(--white); }
  .practice-name {
    font-size: 22px; line-height: 28px; text-align: center; color: var(--white);
  }

  .card-back {
    left: 262px; top: 653px;
    background: linear-gradient(180deg, var(--navy-light) 0%, var(--navy-deep) 100%);
  }
  .back-mark {
    position: absolute; left: 0; top: 120px; width: 100%;
    display: flex; flex-direction: column; align-items: center; gap: 14px;
  }
  .back-dot { width: 18px; height: 18px; border-radius: 50%; background: var(--emboss); }
  .back-name { font-size: 24px; line-height: 30px; text-align: center; color: var(--emboss); }
  .slogan {
    position: absolute; left: 0; top: 336px; width: 100%; text-align: center;
    font-size: 16px; letter-spacing: 3.4px; color: var(--gold);
  }
</style>
</head>
<body>
  <section class="card card-front">
    <div class="front-band"></div>
    <h1 class="doctor-name">LYDIA VANCE, M.D.</h1>
    <p class="doctor-title">Board Certified Hand and<br>Upper Extremity Surgeon</p>

    <div class="contact">
      <p class="address">38517 North Willowmere Ave<br>Maple Hollow, FL 33990</p>
      <ul class="contact-list">
        <li><svg viewBox="0 0 24 24" aria-hidden="true"><path d="M6.6 10.8a15.1 15.1 0 0 0 6.6 6.6l2.2-2.2a1 1 0 0 1 1-.25 11.4 11.4 0 0 0 3.6.57 1 1 0 0 1 1 1V20a1 1 0 0 1-1 1A17 17 0 0 1 3 4a1 1 0 0 1 1-1h3.5a1 1 0 0 1 1 1c0 1.250.2 2.45.57 3.57a1 1 0 0 1-.25 1z"/></svg>954-218-4063</li>
        <li><svg viewBox="0 0 24 24" aria-hidden="true"><path d="M7 2h10v5H7zM4 8h16a2 2 0 0 1 2 2v7h-4v5H6v-5H2v-7a2 2 0 0 1 2-2zm4 8v4h8v-4z"/></svg>954-582-7341</li>
        <li><svg viewBox="0 0 24 24" aria-hidden="true"><path d="M2 5h20v14H2zm2 2v.5l8 5.5 8-5.5V7z"/></svg>info@myrvbonecare.example</li>
        <li><svg viewBox="0 0 24 24" aria-hidden="true"><path d="M12 2a10 10 0 1 0 0 20 10 10 0 0 0 0-20zm-1 17.9A8 8 0 0 1 4.1 11H7v2l4 4zm6.9-2.5A2 2 0 0 0 16 16h-1v-3a1 1 0 0 0-1-1H8v-2h2a1 1 0 0 0 1-1V7h2a2 2 0 0 0 2-2v-.4a8 8 0 0 1 2.9 12.8z"/></svg>www.myrvbonecare.example</li>
      </ul>
    </div>

    <div class="practice-mark">
      <span class="practice-dot"></span>
      <span class="practice-name">RV Bone &amp; Vitality Center</span>
    </div>
  </section>

  <section class="card card-back">
    <div class="back-mark">
      <span class="back-dot"></span>
      <p class="back-name">RV Bone &amp; Vitality Center</p>
    </div>
    <p class="slogan">GROUNDED IN CARE. CENTERED ON YOU</p>
  </section>
</body>
</html>
```